Varnik Holdings — Business Card Design Brief
Overview
Design a double-sided business card for Varnik Holdings that highlights our two service arms: Varnik Communications (telecommunications) and Varnik Energy (business energy solutions). The card should feel smart and stand out when handed to clients.

Objectives
Showcase our areas of specialty clearly.
Reflect the overall Varnik / Varnik Holdings brand while acknowledging both arms.
Explore using both logos (Communications + Energy) or one unified logo, depending on the design.

Deliverables
One double-sided business card design (front + back).

Content & Copy
Front (preferred): Logo: Varnik / Varnik Holdings
Descriptor: Business Communications | Business Energy
Back:My contact details and company details
Core products: Business Mobile • Telephony • Internet • Business Energy Solutions

Brand & Visual Direction
We have a group logo currently tailored more toward telecoms, plus a separate Varnik Energy logo.
Please explore layouts that use both logos or just one, whichever works best.
Color: I wouldn't mind seeing an option using our the Blue/Purple gradient from our website (varnik-example.co.uk), but also open to non-gradient approaches and other colours..

Overall look: Smart, modern, and distinctive.
Format & Print Specs
Double-sided business card format. (Use a standard size

Must-Haves
Front: Varnik wording or Varnik Holdings wording with atleast 1 logo also on front “Business Communications | Business Energy.”

Back: Contact + company details and core products.
A design that stands out while remaining professional.

Nice-to-Have Options
A gradient version using our site’s Blue/Purple gradient.
A non-gradient version.
A dual-logo treatment versus a single-logo treatment.

Thanks
Owen

```html
<!DOCTYPE html>
<html lang="en">
<head>
<meta charset="utf-8">
<title>Varnik Holdings — Business Card</title>
<link rel="stylesheet" href="https://fonts.googleapis.com/css2?family=Poppins:wght@300;400;500;700;800&display=swap">
<style>
  :root {
    --stage: #1c1c1f;
    --navy: #1d1564;
    --ink: #1b1a5e;
    --blue: #1f5fd6;
    --cyan: #0db4e4;
    --band-start: #3b5fb8;
    --band-end: #0cb6e6;
    --paper: #ffffff;
  }
  * { margin: 0; padding: 0; box-sizing: border-box; }
  html, body { width: 1200px; height: 1200px; overflow: hidden; }
  body {
    background: var(--stage);
    font-family: "Poppins", sans-serif;
    display: flex;
    flex-direction: column;
    align-items: center;
    justify-content: center;
    gap: 44px;
  }
  .card {
    width: 900px;
    height: 514px;
    position: relative;
    overflow: hidden;
    box-shadow: 0 14px 40px rgba(0,0,0,.55);
  }

  /* Front */
  .card-front {
    background: var(--navy);
    display: flex;
    flex-direction: column;
    align-items: center;
    justify-content: center;
  }
  .brand-dot {
    width: 150px; height: 150px; border-radius: 50%;
    background: linear-gradient(135deg, var(--blue), var(--cyan));
  }
  .card-front .brand-dot { margin-bottom: 34px; }
  .front-name {
    color: var(--paper);
    font-weight: 800;
    font-size: 56px;
    letter-spacing: 3px;
    line-height: 1.1;
  }
  .front-descriptor {
    margin-top: 14px;
    color: var(--cyan);
    font-weight: 400;
    font-size: 22px;
    letter-spacing: 2px;
  }

  /* Back */
  .card-back { background: var(--paper); }
  .accent-tab {
    position: absolute; left: 0; top: 52px;
    width: 26px; height: 52px;
    background: linear-gradient(180deg, var(--cyan), var(--blue));
  }
  .person { position: absolute; left: 64px; top: 50px; }
  .person-name {
    color: var(--blue);
    font-weight: 700; font-size: 34px; letter-spacing: 1.5px; line-height: 1.1;
  }
  .person-title {
    color: var(--ink);
    font-weight: 300; font-size: 20px; letter-spacing: 2px;
  }
  .address {
    position: absolute; left: 64px; top: 170px;
    color: var(--ink); font-size: 23px; line-height: 1.35;
  }
  .contact-list {
    position: absolute; left: 40px; top: 268px;
    list-style: none; color: var(--ink); font-size: 24px;
  }
  .contact-list li { display: flex; align-items: center; gap: 14px; height: 38px; }
  .contact-icon { width: 28px; height: 28px; flex: none; }
  .back-brand {
    position: absolute; right: 70px; top: 120px;
    display: flex; flex-direction: column; align-items: center; gap: 20px;
  }
  .back-brand .brand-dot { width: 120px; height: 120px; }
  .back-name {
    color: var(--ink); font-weight: 800; font-size: 66px; letter-spacing: 3px; line-height: 1;
  }
  .product-band {
    position: absolute; left: 0; right: 0; bottom: 44px; height: 62px;
    background: linear-gradient(90deg, var(--band-start), var(--band-end));
    color: var(--paper);
    font-size: 25px; font-weight: 500; letter-spacing: .5px;
    display: flex; align-items: center; justify-content: center;
  }
</style>
</head>
<body>
  <section class="card card-front">
    <div class="brand-dot"></div>
    <div class="front-name">VARNIK HOLDINGS</div>
    <div class="front-descriptor">Business Communications | Business Energy</div>
  </section>

  <section class="card card-back">
    <div class="accent-tab"></div>
    <div class="person">
      <div class="person-name">DANIEL R HOLLOWAY</div>
      <div class="person-title">BUSINESS DEVELOPMENT MANAGER</div>
    </div>
    <div class="address">2140 Harbor Lane ste 310<br>Marlow WA 54321</div>
    <ul class="contact-list">
      <li>
        <svg class="contact-icon" viewBox="0 0 28 28"><circle cx="14" cy="14" r="14" fill="#1f8fd8"/><path d="M10 8c1 0 2 2.5 2 3s-1 1-1 1.5c0 1 3 4 4 4 .5 0 1-1 1.5-1s3 1 3 2-1.5 2.5-3 2.5C12 20 8 16 8 11c0-1.5 1-3 2-3z" fill="#fff"/></svg>
        (555) 014-2297
      </li>
      <li>
        <svg class="contact-icon" viewBox="0 0 28 28"><circle cx="14" cy="14" r="14" fill="#1f8fd8"/><rect x="7" y="9" width="14" height="10" rx="1" fill="#fff"/><path d="M7 9l7 6 7-6" fill="none" stroke="#1f8fd8" stroke-width="1.3"/></svg>
        daniel@varnik-example.co.uk
      </li>
      <li>
        <svg class="contact-icon" viewBox="0 0 28 28"><circle cx="14" cy="14" r="14" fill="#1f8fd8"/><g fill="none" stroke="#fff" stroke-width="1.3"><circle cx="14" cy="14" r="7"/><ellipse cx="14" cy="14" rx="3" ry="7"/><path d="M7 14h14M8.5 10.5h11M8.5 17.5h11"/></g></svg>
        www.varnik-example.co.uk
      </li>
    </ul>
    <div class="back-brand">
      <div class="brand-dot"></div>
      <div class="back-name">VARNIK</div>
    </div>
    <div class="product-band">Business Mobile • Telephony • Internet • Business Energy Solutions</div>
  </section>
</body>
</html>
```